Dental-Specific Brochure for IT Services

We are creating a brochure for IT services for local dental practices. Highlights should include:
- no contract / we earn your business on a month to month basis
- affordable pricing
- fast response times
- 25+ local dental practices
- predictable fixed-rate billing
Text should include:
Why Dental Practices Choose WPAX?At WPAX, we specialize in providing reliable, affordable, and high-quality IT solutions tailored specifically for dental offices. With over 25 local dental practices trusting us with their IT needs, we understand the unique challenges you face and offer solutions to keep your practice running smoothly.
What Sets WPAX Apart?
✅ No Contracts – We believe in earning your business every month. Stay because you want to, not because you have to.
✅ Affordable Pricing – Cost-effective solutions that fit your budget without sacrificing quality.
✅ Fast Response Times – When you need IT support, we’re there. Minimize downtime and keep your practice operational.
✅ Predictable Fixed-Rate Billing – No surprises, just straightforward pricing that makes budgeting easy.
✅ Proven Track Record – Over 25 dental practices in the area trust WPAX for their IT support.
✅ Expert Cybersecurity & Ransomware Protection – Advanced security measures to protect patient data and experience with HIPAA HITECH Act.
✅ Full Support for Practice Management Software – We work with Hollin Dental, Murvaplex, Quavolo, and other leading platforms.
Our IT Services for Dental Practices:
VoIP Phone Solutions – Reliable communication for your front desk and patient calls.
Managed IT Support – Proactive monitoring, maintenance, and troubleshooting to prevent downtime.
Cloud Solutions – Secure, scalable storage and software solutions for your practice.
Network & Wi-Fi Optimization – Fast, secure, and reliable internet for your office.
High-Speed Fiber Internet – Ensure fast and reliable connectivity to keep your practice running smoothly.
Let’s Get Started!
Join the growing number of dental practices that trust WPAX for their IT needs. Contact us today to schedule a consultation and see how we can help your practice thrive.
-
We would like contact info displayed similarly to how it is on the other brochure in the attachments. I will also be adding some more pictures to use; feel free to add in holding spots for pictures similar to what is in the example brochure.
Logo is in attachments along with current brochure.

```html
<!DOCTYPE html>
<html lang="en">
<head>
<meta charset="utf-8">
<title>WPAX – IT Services for Dental Practices</title>
<link rel="stylesheet" href="https://fonts.googleapis.com/css2?family=Montserrat:wght@400;500;600;700&family=Oswald:wght@600&display=swap">
<style>
  :root {
    --navy: #1c2b8f;
    --navy-deep: #0a1460;
    --navy-mid: #1a2ea6;
    --green: #7dc242;
    --ink: #2a2a2a;
    --white: #ffffff;
    --photo-a: #cfd6e4;
    --photo-b: #8b97b3;
  }
  * { box-sizing: border-box; margin: 0; padding: 0; }
  html, body { width: 912px; height: 1200px; overflow: hidden; background: var(--white); }
  body { font-family: "Montserrat", sans-serif; color: var(--ink); }
  .flyer { position: relative; width: 912px; height: 1200px; overflow: hidden; background: var(--white); }

  /* Hero */
  .hero {
    position: absolute; left: 0; top: 0; width: 912px; height: 544px;
    background: radial-gradient(ellipse at 35% 70%, #2340c8 0%, var(--navy-mid) 30%, var(--navy-deep) 80%);
  }
  .brand-name {
    position: absolute; left: 54px; top: 42px;
    font-family: "Montserrat", sans-serif; font-weight: 600; font-size: 96px;
    line-height: 1; color: var(--white); letter-spacing: -3px;
  }
  .hero-phone {
    position: absolute; left: 408px; top: 43px; width: 160px; height: 139px;
    border-radius: 10px;
    background: linear-gradient(160deg, #4a5160 0%, #22262f 100%);
  }
  .hero-title {
    position: absolute; left: 54px; top: 198px;
    font-family: "Oswald", sans-serif; font-weight: 600; font-size: 48px;
    line-height: 52px; color: var(--white); text-transform: uppercase; letter-spacing: 0.3px;
  }
  .hero-title .accent { color: var(--green); }
  .hero-intro {
    position: absolute; left: 54px; top: 317px; width: 420px;
    font-size: 16.6px; font-weight: 500; line-height: 21.7px; color: var(--white);
  }
  .photo-diamonds { position: absolute; left: 0; top: 0; width: 912px; height: 600px; }

  /* Columns */
  .column-rule { position: absolute; left: 452px; top: 583px; width: 2px; height: 530px; background: var(--green); }
  .section-title {
    position: absolute; font-weight: 700; font-size: 28px; line-height: 34px; color: var(--navy);
  }
  .feature { position: absolute; }
  .feature-title {
    position: relative; font-weight: 700; font-size: 16.5px; line-height: 18px;
    color: var(--green); padding-left: 25px;
  }
  .feature-title .tick { position: absolute; left: 0; top: 1px; width: 17px; height: 17px; }
  .feature-text { padding-left: 25px; margin-top: 2px; font-size: 13.6px; line-height: 16.5px; color: var(--ink); }

  .apart .feature { left: 32px; width: 420px; }
  .services .feature { left: 466px; width: 420px; }

  .cta-text {
    position: absolute; left: 466px; top: 1037px; width: 402px;
    font-size: 13.6px; line-height: 16.5px; text-align: justify; color: var(--ink);
  }

  /* Footer */
  .contact-bar { position: absolute; left: 0; top: 1143px; width: 912px; height: 57px; }
  .contact-bar svg { position: absolute; left: 0; top: 0; }
  .contact-phone {
    position: absolute; left: 38px; top: 0; height: 57px; line-height: 57px;
    font-weight: 700; font-size: 30px; color: var(--white); letter-spacing: 0.3px;
  }
  .contact-web {
    position: absolute; left: 640px; top: 0; height: 57px; line-height: 57px;
    font-weight: 700; font-size: 21px; color: var(--white);
  }
</style>
</head>
<body>
<main class="flyer">

  <header class="hero">
    <div class="brand-name">wpax</div>
    <div class="hero-phone" role="img" aria-label="Photo of a desk VoIP phone"></div>
    <h1 class="hero-title">Why Dental<br>Practices <span class="accent">Choose WPAX?</span></h1>
    <p class="hero-intro">At WPAX, we specialize in providing reliable, affordable, and high-quality IT solutions tailored specifically for dental offices. With over 25 local dental practices trusting us with their IT needs, we understand the unique challenges you face and offer solutions to keep your practice running smoothly.</p>
  </header>

  <svg class="photo-diamonds" viewBox="0 0 912 600" xmlns="http://www.w3.org/2000/svg">
    <defs>
      <linearGradient id="photoTone" x1="0" y1="0" x2="1" y2="1">
        <stop offset="0" stop-color="#dfe5ef"/>
        <stop offset="1" stop-color="#8d9ab6"/>
      </linearGradient>
      <linearGradient id="photoToneWarm" x1="0" y1="0" x2="1" y2="1">
        <stop offset="0" stop-color="#e8e4df"/>
        <stop offset="1" stop-color="#9aa3b5"/>
      </linearGradient>
    </defs>
    <g role="img" aria-label="Photo of a smiling receptionist on the phone">
      <rect x="-92" y="-92" width="184" height="184" rx="26" transform="translate(718 130) rotate(45)" fill="var(--green)"/>
      <rect x="-92" y="-92" width="184" height="184" rx="26" transform="translate(708 128) rotate(45)" fill="url(#photoToneWarm)"/>
    </g>
    <g role="img" aria-label="Photo of office staff on phone headsets">
      <rect x="-108" y="-108" width="216" height="216" rx="28" transform="translate(870 268) rotate(45)" fill="var(--green)"/>
      <rect x="-108" y="-108" width="216" height="216" rx="28" transform="translate(862 266) rotate(45)" fill="url(#photoTone)"/>
    </g>
    <g role="img" aria-label="Photo of a hand using a touchscreen desk phone">
      <rect x="-118" y="-118" width="236" height="236" rx="30" transform="translate(672 426) rotate(45)" fill="var(--green)"/>
      <rect x="-118" y="-118" width="236" height="236" rx="30" transform="translate(664 424) rotate(45)" fill="url(#photoTone)"/>
    </g>
  </svg>

  <div class="column-rule"></div>

  <section class="apart">
    <h2 class="section-title" style="left:32px; top:582px;">What Sets WPAX Apart?</h2>

    <div class="feature" style="top:627px;">
      <h3 class="feature-title"><svg class="tick" viewBox="0 0 20 20"><path d="M17 8.5A7.5 7.5 0 1 1 13 3.3" fill="none" stroke="var(--green)" stroke-width="2.2" stroke-linecap="round"/><path d="M6 9.5l3.5 3.5L18 4" fill="none" stroke="var(--green)" stroke-width="2.6" stroke-linecap="round" stroke-linejoin="round"/></svg>No Contracts</h3>
      <p class="feature-text">We believe in earning your business every month. Stay because you want to, not because you have to.</p>
    </div>
    <div class="feature" style="top:687px;">
      <h3 class="feature-title"><svg class="tick" viewBox="0 0 20 20"><path d="M17 8.5A7.5 7.5 0 1 1 13 3.3" fill="none" stroke="var(--green)" stroke-width="2.2" stroke-linecap="round"/><path d="M6 9.5l3.5 3.5L18 4" fill="none" stroke="var(--green)" stroke-width="2.6" stroke-linecap="round" stroke-linejoin="round"/></svg>Affordable Pricing</h3>
      <p class="feature-text">Cost-effective solutions that fit your budget without sacrificing quality.</p>
    </div>
    <div class="feature" style="top:747px;">
      <h3 class="feature-title"><svg class="tick" viewBox="0 0 20 20"><path d="M17 8.5A7.5 7.5 0 1 1 13 3.3" fill="none" stroke="var(--green)" stroke-width="2.2" stroke-linecap="round"/><path d="M6 9.5l3.5 3.5L18 4" fill="none" stroke="var(--green)" stroke-width="2.6" stroke-linecap="round" stroke-linejoin="round"/></svg>Fast Response Times</h3>
      <p class="feature-text">When you need IT support, we’re there. Minimize downtime and keep your practice operational.</p>
    </div>
    <div class="feature" style="top:812px;">
      <h3 class="feature-title"><svg class="tick" viewBox="0 0 20 20"><path d="M17 8.5A7.5 7.5 0 1 1 13 3.3" fill="none" stroke="var(--green)" stroke-width="2.2" stroke-linecap="round"/><path d="M6 9.5l3.5 3.5L18 4" fill="none" stroke="var(--green)" stroke-width="2.6" stroke-linecap="round" stroke-linejoin="round"/></svg>Predictable Fixed-Rate Billing</h3>
      <p class="feature-text">No surprises, just straightforward pricing that makes budgeting easy.</p>
    </div>
    <div class="feature" style="top:877px;">
      <h3 class="feature-title"><svg class="tick" viewBox="0 0 20 20"><path d="M17 8.5A7.5 7.5 0 1 1 13 3.3" fill="none" stroke="var(--green)" stroke-width="2.2" stroke-linecap="round"/><path d="M6 9.5l3.5 3.5L18 4" fill="none" stroke="var(--green)" stroke-width="2.6" stroke-linecap="round" stroke-linejoin="round"/></svg>Proven Track Record</h3>
      <p class="feature-text">Over 25 dental practices in the area trust WPAX for their IT support.</p>
    </div>
    <div class="feature" style="top:944px;">
      <h3 class="feature-title" style="line-height:20px;"><svg class="tick" viewBox="0 0 20 20"><path d="M17 8.5A7.5 7.5 0 1 1 13 3.3" fill="none" stroke="var(--green)" stroke-width="2.2" stroke-linecap="round"/><path d="M6 9.5l3.5 3.5L18 4" fill="none" stroke="var(--green)" stroke-width="2.6" stroke-linecap="round" stroke-linejoin="round"/></svg>Expert Cybersecurity &amp;<br>Ransomware Protection</h3>
      <p class="feature-text">Advanced security measures to protect patient data and experience with HIPAA HITECH Act.</p>
    </div>
    <div class="feature" style="top:1032px;">
      <h3 class="feature-title" style="line-height:20px;"><svg class="tick" viewBox="0 0 20 20"><path d="M17 8.5A7.5 7.5 0 1 1 13 3.3" fill="none" stroke="var(--green)" stroke-width="2.2" stroke-linecap="round"/><path d="M6 9.5l3.5 3.5L18 4" fill="none" stroke="var(--green)" stroke-width="2.6" stroke-linecap="round" stroke-linejoin="round"/></svg>Full Support for Practice<br>Management Software</h3>
      <p class="feature-text">We work with Hollin Dental, Murvaplex, Quavolo, and other leading platforms.</p>
    </div>
  </section>

  <section class="services">
    <h2 class="section-title" style="left:466px; top:582px;">Our IT Services<br>for Dental Practices:</h2>

    <div class="feature" style="top:659px;">
      <h3 class="feature-title"><svg class="tick" viewBox="0 0 20 20"><path d="M17 8.5A7.5 7.5 0 1 1 13 3.3" fill="none" stroke="var(--green)" stroke-width="2.2" stroke-linecap="round"/><path d="M6 9.5l3.5 3.5L18 4" fill="none" stroke="var(--green)" stroke-width="2.6" stroke-linecap="round" stroke-linejoin="round"/></svg>VoIP Phone Solutions</h3>
      <p class="feature-text">Reliable communication for your front desk and patient calls.</p>
    </div>
    <div class="feature" style="top:718px;">
      <h3 class="feature-title"><svg class="tick" viewBox="0 0 20 20"><path d="M17 8.5A7.5 7.5 0 1 1 13 3.3" fill="none" stroke="var(--green)" stroke-width="2.2" stroke-linecap="round"/><path d="M6 9.5l3.5 3.5L18 4" fill="none" stroke="var(--green)" stroke-width="2.6" stroke-linecap="round" stroke-linejoin="round"/></svg>Managed IT Support</h3>
      <p class="feature-text">Proactive monitoring, maintenance, and troubleshooting to prevent downtime.</p>
    </div>
    <div class="feature" style="top:775px;">
      <h3 class="feature-title"><svg class="tick" viewBox="0 0 20 20"><path d="M17 8.5A7.5 7.5 0 1 1 13 3.3" fill="none" stroke="var(--green)" stroke-width="2.2" stroke-linecap="round"/><path d="M6 9.5l3.5 3.5L18 4" fill="none" stroke="var(--green)" stroke-width="2.6" stroke-linecap="round" stroke-linejoin="round"/></svg>Cloud Solutions</h3>
      <p class="feature-text">Secure, scalable storage and software solutions for your practice.</p>
    </div>
    <div class="feature" style="top:837px;">
      <h3 class="feature-title"><svg class="tick" viewBox="0 0 20 20"><path d="M17 8.5A7.5 7.5 0 1 1 13 3.3" fill="none" stroke="var(--green)" stroke-width="2.2" stroke-linecap="round"/><path d="M6 9.5l3.5 3.5L18 4" fill="none" stroke="var(--green)" stroke-width="2.6" stroke-linecap="round" stroke-linejoin="round"/></svg>Network &amp; Wi-Fi Optimization</h3>
      <p class="feature-text">Fast, secure, and reliable internet for your office.</p>
    </div>
    <div class="feature" style="top:878px;">
      <h3 class="feature-title"><svg class="tick" viewBox="0 0 20 20"><path d="M17 8.5A7.5 7.5 0 1 1 13 3.3" fill="none" stroke="var(--green)" stroke-width="2.2" stroke-linecap="round"/><path d="M6 9.5l3.5 3.5L18 4" fill="none" stroke="var(--green)" stroke-width="2.6" stroke-linecap="round" stroke-linejoin="round"/></svg>High-Speed Fiber Internet</h3>
      <p class="feature-text">Ensure fast and reliable connectivity to keep your practice running smoothly.</p>
    </div>

    <h2 class="section-title" style="left:466px; top:993px;">Let’s Get Started!</h2>
    <p class="cta-text">Join the growing number of dental practices that trust WPAX for their IT needs. Contact us today to schedule a consultation and see how we can help your practice thrive.</p>
  </section>

  <footer class="contact-bar">
    <svg width="912" height="57" viewBox="0 0 912 57" xmlns="http://www.w3.org/2000/svg" aria-hidden="true">
      <rect width="912" height="57" fill="var(--navy)"/>
      <polygon points="557,0 912,0 912,57 486,57" fill="var(--green)"/>
    </svg>
    <div class="contact-phone">CALL NOW 555-014-2286</div>
    <div class="contact-web">www.gowpax.com</div>
  </footer>

</main>
</body>
</html>
```